Two Versions of a Business Card for a Lawyer

Summary: I need a logo and a business card. The business card is two-sided and comes in two versions. One version is conservative, the other is slightly different with one or more pink embellishments in the logo or somewhere else in the business card.
I'm about to start off as a sole practitioner in criminal and immigration law. I'll largely be working with marginalised communities and in areas of social justice. One of my main focuses will be gendered violence, I'm hoping to specialise my practice towards representing victims of domestic and sexual violence and sex workers. I want a business card which would attract this clientele and make them feel safe to speak with me. I'd also like it to communicate a sense of hope.
However, the business card still has to be very conservative as the legal profession is very stuffy. So I was thinking of having two versions of the same card, one would be very straight forward while the other would have a **pink embellishment** or perhaps several. For example, if the scales of justice were used in the design, maybe the second version would have a pink flower about to bloom on the scale somewhere. Or maybe it's my logo that is different and pink.
While both designs have to be pretty conservative, I still want it to give off a sense that I'm alternative and think outside the box. With lawyers, I think a little bit of deviation goes a long way (less is more).
As far as colour goes (other than the pink embellishment), I was thinking something monochromatic, probably black and white but I am open to considering more colours. I personally love colour, and would love to use more colour, but am hesitant because of the nature of the profession. If you can find a way to use more colour while keeping it conservative and letting the pink pop, I'd be pretty pleased.
In general, I would prefer a clean simplistic design and logo. It should be immediately obvious that I'm a lawyer just by glancing at the card. I'm open to symbols of law, like the scales of justice or lady justice or something else. However, I don't want it to be the same as everyone else's.
Eventually, the design/style should be easy to recreate in the form of a website.
As far as the logo goes, it would probably use a circle as my last name starts with the letter "O". It can be very simple, with just my name and "Barrister & Solicitor". I don't currently have a logo, but the winning designer will be invited to provide a separate file for just the logo for an additional fee (I think it was CA$99). (Please ignore the uploaded logo file, it just wouldn't let me continue without uploading something).
As for the information that should go into the card, I'm still finalizing my address and phone number. So please use a placeholder for now.
Target Market(s)
Women, victims of sexual or domestic violence, refugees, people in need of legal services
Industry/Entity Type
Lawyer
Contact Information for Business Card
Marla Vent
Barrister & Solicitor
LL.B., B.C.L., B.F.A.
Criminal & Immigration Law
Street address
Toronto, ON
Postal Code
Phone number
Fax number
Email
Logo Text
Marla Vent, Barrister & Solicitor
Requirements
Must have
- Two versions
- One with pink
- Simplistic
Nice to have
- Maybe more colour
Should not have
- Not too conservative
- Not too predictable

```html
<!DOCTYPE html>
<html lang="en">
<head>
<meta charset="utf-8">
<title>Marla Vent — Barrister &amp; Solicitor</title>
<link rel="stylesheet" href="https://fonts.googleapis.com/css2?family=Crimson+Pro:ital,wght@1,500;1,700&display=swap">
<style>
  :root {
    --ink: #111111;
    --paper: #f4f4f4;
    --paper-shade: #e6e6e6;
    --accent-pink: #d8195c;
    --footer-bg: #1a1a1a;
    --footer-text: #ffffff;
  }
  html, body {
    margin: 0;
    padding: 0;
    overflow: hidden;
    background: #ffffff;
  }
  .card {
    position: relative;
    width: 1200px;
    height: 686px;
    overflow: hidden;
    font-family: "Crimson Pro", "Palatino Linotype", Georgia, serif;
    font-style: italic;
    color: var(--ink);
  }
  .card__texture {
    position: absolute;
    inset: 0;
    background: linear-gradient(180deg, var(--paper) 0%, var(--paper-shade) 100%);
  }
  .identity {
    position: absolute;
    left: 0;
    right: 0;
    top: 0;
    text-align: center;
  }
  .identity__name {
    position: absolute;
    left: 0; right: 0;
    top: 112px;
    margin: 0;
    font-size: 96px;
    font-weight: 500;
    line-height: 1;
    letter-spacing: 1px;
  }
  .identity__title,
  .identity__degrees {
    position: absolute;
    left: 0; right: 0;
    margin: 0;
    font-size: 38px;
    font-weight: 700;
    line-height: 1;
  }
  .identity__title { top: 212px; }
  .identity__degrees { top: 258px; }
  .identity__practice {
    position: absolute;
    left: 0; right: 0;
    top: 330px;
    margin: 0;
    font-size: 48px;
    font-weight: 700;
    line-height: 1;
  }
  .divider {
    position: absolute;
    left: 270px;
    top: 410px;
  }
  .address {
    position: absolute;
    left: 0; right: 0;
    top: 446px;
    text-align: center;
    color: var(--accent-pink);
    font-size: 23px;
    font-weight: 700;
    line-height: 43px;
  }
  .address p { margin: 0; }
  .contact-bar {
    position: absolute;
    left: 0;
    right: 0;
    bottom: 0;
    height: 64px;
    background: var(--footer-bg);
    color: var(--footer-text);
    font-size: 23px;
    font-weight: 700;
  }
  .contact-bar__item {
    position: absolute;
    top: 18px;
    margin: 0;
  }
  .contact-bar__item--fax { left: 80px; }
  .contact-bar__item--phone { left: 377px; }
  .contact-bar__item--email { left: 724px; }
</style>
</head>
<body>
  <main class="card">
    <div class="card__texture" role="img" aria-label="Light white brick wall texture"></div>

    <header class="identity">
      <h1 class="identity__name">Marla Vent</h1>
      <p class="identity__title">Barrister &amp; Solicitor</p>
      <p class="identity__degrees">LL.B., B.C.L., B.F.A.</p>
      <p class="identity__practice">Criminal &amp; Immigration Law</p>
    </header>

    <svg class="divider" width="660" height="8" viewBox="0 0 660 8" aria-hidden="true">
      <defs>
        <linearGradient id="divider-fade" x1="0" x2="1" y1="0" y2="0">
          <stop offset="0" stop-color="var(--accent-pink)" stop-opacity="0"/>
          <stop offset="0.2" stop-color="var(--accent-pink)" stop-opacity="1"/>
          <stop offset="0.8" stop-color="var(--accent-pink)" stop-opacity="1"/>
          <stop offset="1" stop-color="var(--accent-pink)" stop-opacity="0"/>
        </linearGradient>
      </defs>
      <rect x="0" y="2" width="660" height="4" rx="2" fill="url(#divider-fade)"/>
    </svg>

    <address class="address">
      <p>Street address</p>
      <p>Toronto, ON</p>
    </address>

    <footer class="contact-bar">
      <p class="contact-bar__item contact-bar__item--fax">Fax number</p>
      <p class="contact-bar__item contact-bar__item--phone">Phone number</p>
      <p class="contact-bar__item contact-bar__item--email">Email</p>
    </footer>
  </main>
</body>
</html>
```